Business Card Design

I already have a company logo for my company. I have a logo for the manufacturer we represent. I want a professional business card design.

```html
<!DOCTYPE html>
<html lang="en">
<head>
<meta charset="utf-8">
<title>Hazard Line Partners – Business Card</title>
<link rel="stylesheet" href="https://fonts.googleapis.com/css2?family=Arimo:wght@400;700&display=swap">
<style>
  :root {
    --stage: #2d2d2d;
    --card: #000000;
    --red: #e5202e;
    --gold: #d4a514;
    --white: #ffffff;
  }
  * { box-sizing: border-box; margin: 0; padding: 0; }
  html, body {
    width: 1200px; height: 1015px; overflow: hidden;
    background: var(--stage);
    font-family: "Arimo", Arial, sans-serif;
  }
  .sheet {
    position: relative; width: 1200px; height: 1015px;
    display: flex; flex-direction: column; align-items: center; justify-content: center; gap: 50px;
  }
  .card {
    position: relative; width: 700px; height: 400px;
    background: var(--card);
    box-shadow: 0 12px 30px rgba(0,0,0,.55);
    overflow: hidden;
  }
  .card__edge {
    position: absolute; left: 0; right: 0; bottom: 0; height: 9px;
    background: var(--red);
  }
  /* Front */
  .front { display: flex; align-items: center; justify-content: center; }
  .brand { display: flex; align-items: center; gap: 14px; }
  .brand__square { width: 26px; height: 26px; background: var(--red); }
  .brand__name {
    color: var(--white); font-weight: 700; font-size: 38px; letter-spacing: 2px;
    text-transform: uppercase;
  }
  /* Back */
  .back__brand { position: absolute; right: 50px; top: 70px; }
  .back__brand .brand__name { font-size: 24px; letter-spacing: 1.5px; }
  .back__brand .brand__square { width: 18px; height: 18px; }
  .details { position: absolute; left: 70px; top: 150px; color: var(--white); }
  .details__name { color: var(--red); font-weight: 700; font-size: 26px; letter-spacing: .5px; }
  .details__role { font-size: 16px; letter-spacing: .5px; margin-top: 2px; }
  .rule { width: 130px; height: 1.5px; background: var(--gold); margin: 16px 0 14px; }
  .contacts { list-style: none; }
  .contacts li { display: flex; align-items: center; gap: 10px; font-size: 18px; line-height: 26px; }
  .contacts svg { width: 16px; height: 16px; flex: none; }
  .address { font-size: 18px; line-height: 24px; }
</style>
</head>
<body>
<main class="sheet">
  <section class="card front" aria-label="Card front">
    <div class="brand">
      <span class="brand__square"></span>
      <span class="brand__name">Hazard Line Partners</span>
    </div>
    <div class="card__edge"></div>
  </section>

  <section class="card back" aria-label="Card back">
    <div class="brand back__brand">
      <span class="brand__square"></span>
      <span class="brand__name">Hazard Line Partners</span>
    </div>
    <div class="details">
      <p class="details__name">DANIEL REYES</p>
      <p class="details__role">MANAGING DIRECTOR</p>
      <div class="rule"></div>
      <ul class="contacts">
        <li>
          <svg viewBox="0 0 24 24" fill="var(--red)" aria-hidden="true"><path d="M6.6 10.8a15.1 15.1 0 0 0 6.6 6.6l2.2-2.2a1 1 0 0 1 1-.25 11.4 11.4 0 0 0 3.6.57 1 1 0 0 1 1 1V20a1 1 0 0 1-1 1A17 17 0 0 1 3 4a1 1 0 0 1 1-1h3.5a1 1 0 0 1 1 1c0 1.25.2 2.45.57 3.57a1 1 0 0 1-.25 1z"/></svg>
          055-310 872 416
        </li>
        <li>
          <svg viewBox="0 0 24 24" fill="var(--red)" aria-hidden="true"><path d="M2 5h20v14H2z M4 7v.4l8 5.2 8-5.2V7z" fill-rule="evenodd"/></svg>
          hello@hazardline.co
        </li>
        <li>
          <svg viewBox="0 0 24 24" fill="none" stroke="var(--red)" stroke-width="2" aria-hidden="true"><circle cx="12" cy="12" r="9"/><path d="M3 12h18M12 3c3 3 3 15 0 18M12 3c-3 3-3 15 0 18"/></svg>
          www.hazardline.co
        </li>
      </ul>
      <div class="rule"></div>
      <p class="address">421, Address line goes here<br>45452, Country Name</p>
    </div>
    <div class="card__edge"></div>
  </section>
</main>
</body>
</html>
```